Vantrel Intergrated Marketing Stationary Design Contest

We require a very professional looking stationary set to include: letterhead, compliments slip and business cards (double sided bus cards).

Files should be supplied on either Illustrator or InDesign.

We are interested in perhaps encorporating a faint watermark with the letter q or the logo, but it isnt a pre-requisite

Target Market(s)

Business owners seeking professional marketing services

Industry/Entity Type

Marketing

Requirements
Must have
• Concurrent theme wiht business cards, letterhead and comp slip. Must be an editable document for future ammendment
Should not have
• No use of times new roman or similar fonts

```html
<!DOCTYPE html>
<html lang="en">
<head>
<meta charset="utf-8">
<title>Vantrel Integrated Marketing – Business Card</title>
<link rel="stylesheet" href="https://fonts.googleapis.com/css2?family=Questrial&display=swap">
<style>
  :root {
    --brand-orange: #e65021;
    --ink: #111111;
    --paper: #ffffff;
    --trim-line: #1a1a1a;
  }
  * { margin: 0; padding: 0; box-sizing: border-box; }
  html, body {
    width: 1200px;
    height: 600px;
    overflow: hidden;
    background: var(--paper);
  }
  .card {
    position: relative;
    width: 1200px;
    height: 600px;
    overflow: hidden;
    background: var(--paper);
    font-family: "Questrial", "Helvetica Neue", Arial, sans-serif;
    color: var(--ink);
  }
  .card__backdrop {
    position: absolute;
    inset: 0;
  }
  .brand-disc { fill: var(--brand-orange); }
  .trim-mark { stroke: var(--trim-line); stroke-width: 1.5; }

  .signature {
    position: absolute;
    left: 700px;
    top: 458px;
    display: flex;
    align-items: center;
    gap: 28px;
  }
  .signature__dot {
    width: 120px;
    height: 120px;
    border-radius: 50%;
    background: var(--brand-orange);
    flex: none;
  }
  .signature__text {
    display: flex;
    flex-direction: column;
  }
  .signature__name {
    font-size: 66px;
    line-height: 0.9;
    letter-spacing: 0.12em;
    color: var(--ink);
    font-weight: 400;
  }
  .signature__tagline {
    margin-top: 14px;
    font-size: 25px;
    line-height: 1;
    letter-spacing: 0.08em;
    color: var(--ink);
    font-weight: 400;
  }
</style>
</head>
<body>
  <main class="card">
    <svg class="card__backdrop" width="1200" height="600" viewBox="0 0 1200 600" aria-hidden="true">
      <circle class="brand-disc" cx="231" cy="305" r="402"/>
      <line class="trim-mark" x1="601" y1="42" x2="601" y2="90"/>
      <line class="trim-mark" x1="601" y1="138" x2="601" y2="162"/>
      <line class="trim-mark" x1="601" y1="452" x2="601" y2="480"/>
      <line class="trim-mark" x1="601" y1="526" x2="601" y2="574"/>
    </svg>

    <div class="signature">
      <span class="signature__dot" aria-hidden="true"></span>
      <div class="signature__text">
        <span class="signature__name">vantrel</span>
        <span class="signature__tagline">Integrated Marketing</span>
      </div>
    </div>
  </main>
</body>
</html>
```